I'm looking for a smart new design for business cards

Industry/Entity Type

Commercial Electrical

Contact Information for Business Card

Logo, name, email, position, website QR

Requirements
Nice to have
• Logo embedded behind the text side

```html
<!DOCTYPE html>
<html lang="en">
<head>
<meta charset="UTF-8">
<title>Northgate Power Services – Business Card</title>
<link href="https://fonts.googleapis.com/css2?family=Montserrat:wght@700;800&family=Roboto:wght@400;700&display=swap" rel="stylesheet">
<style>
  :root {
    --navy: #0b0f82;
    --red: #e2003a;
    --ink: #111111;
    --muted: #555555;
    --rule: #cfcfcf;
    --paper: #ffffff;
    --backdrop: #e4e4e4;
  }
  * { box-sizing: border-box; margin: 0; padding: 0; }
  html, body { width: 1200px; height: 1200px; overflow: hidden; }
  body { background: var(--backdrop); position: relative; font-family: "Roboto", Arial, sans-serif; }

  .card { position: absolute; width: 687px; height: 392px; border-radius: 22px; overflow: hidden; }
  .card--front { left: 267px; top: 159px; background: var(--paper); }
  .card--back { left: 262px; top: 654px; background: var(--navy); }

  .wordmark { display: flex; align-items: center; gap: 12px; font-family: "Montserrat", Arial, sans-serif; font-weight: 800; line-height: 1; letter-spacing: 2px; }
  .wordmark__square { background: var(--red); }

  .card--front .wordmark { position: absolute; left: 64px; top: 34px; width: 276px; justify-content: center; color: var(--navy); font-size: 84px; }
  .card--front .wordmark__square { width: 30px; height: 30px; }

  .company { font-family: "Montserrat", Arial, sans-serif; font-weight: 700; text-align: center; text-transform: uppercase; line-height: 1.2; }
  .card--front .company { position: absolute; left: 30px; width: 344px; top: 145px; font-size: 19.5px; color: var(--ink); letter-spacing: .3px; }

  .person { position: absolute; left: 55px; top: 222px; }
  .person__name { font-weight: 700; font-size: 27px; color: var(--navy); letter-spacing: .5px; text-transform: uppercase; }
  .person__role { font-size: 16px; color: var(--muted); margin-top: 2px; }

  .divider { position: absolute; left: 53px; top: 278px; width: 422px; height: 1px; background: var(--rule); }

  .contact { position: absolute; top: 296px; font-size: 16.5px; color: #333; line-height: 20px; list-style: none; }
  .contact--reach { left: 51px; }
  .contact--reach li { display: flex; align-items: center; gap: 7px; }
  .contact--reach svg { width: 14px; height: 14px; fill: var(--red); flex: none; }
  .contact--place { left: 229px; top: 298px; }
  .contact__sep { position: absolute; left: 206px; top: 299px; width: 1px; height: 55px; background: #333; }

  .card--back .wordmark { position: absolute; left: 0; right: 0; top: 92px; justify-content: center; color: var(--paper); font-size: 128px; gap: 18px; }
  .card--back .wordmark__square { width: 44px; height: 44px; }
  .card--back .company { position: absolute; left: 0; right: 0; top: 250px; font-size: 27px; color: var(--paper); letter-spacing: .5px; }
</style>
</head>
<body>
  <section class="card card--front">
    <div class="wordmark"><span>NPS</span><span class="wordmark__square"></span></div>
    <p class="company">Northgate Power<br>Services</p>
    <div class="person">
      <h1 class="person__name">Daniel Reyes</h1>
      <p class="person__role">President</p>
    </div>
    <div class="divider"></div>
    <ul class="contact contact--reach">
      <li><svg viewBox="0 0 24 24"><path d="M6.6 10.8a15.1 15.1 0 0 0 6.6 6.6l2.2-2.2a1 1 0 0 1 1-.25 11.4 11.4 0 0 0 3.6.57 1 1 0 0 1 1 1V20a1 1 0 0 1-1 1A17 17 0 0 1 3 4a1 1 0 0 1 1-1h3.5a1 1 0 0 1 1 1c0 1.25.2 2.45.57 3.57a1 1 0 0 1-.25 1z"/></svg>555-201-7480</li>
      <li><svg viewBox="0 0 24 24"><path d="M7 1h10a2 2 0 0 1 2 2v18a2 2 0 0 1-2 2H7a2 2 0 0 1-2-2V3a2 2 0 0 1 2-2zm0 3v15h10V4z"/></svg>555-309-6217</li>
      <li><svg viewBox="0 0 24 24"><path d="M2 5h20v14H2zm2 2v.5l8 5 8-5V7zm0 2.8V17h16V9.8l-8 5z"/></svg>info@NPS.com</li>
    </ul>
    <div class="contact__sep"></div>
    <ul class="contact contact--place">
      <li>412 Harbour Road</li>
      <li>Brookvale, NSW 2100</li>
      <li>www.NPS.com</li>
    </ul>
  </section>

  <section class="card card--back">
    <div class="wordmark"><span>NPS</span><span class="wordmark__square"></span></div>
    <p class="company">Northgate Power<br>Services</p>
  </section>
</body>
</html>
```